Internal Office Slogans / Motto / Vision Statements

Hi. We would like to put up some posters around the office with quotations such as -
-”Do what you do so well that they will want to see it again and bring their friends.”- Hollis Brandt
-Make your customers feel heard and understood. Make your customers feel respected and liked. Make your customers feel appreciated and helped. Understand that you can do none of these things unless you are sincere about them.
Terrence Oakley
- It’s a very predictable and satisfying phenomenon: whenever we get better, our customers do too.
Cal Pruett
-Catch people in the act of performing extraordinary customer service. Treat them like heroes. Tell their stories, far and wide.
Ned Farraday

The purpose of the posters is to reiterate our culture and vision within the organisation. They should be clean, crisp and eye catching, not gaudy or bright. Professional, bold and strong.

The company website and logo is at http://www.nexoraweb.com.au
Print size will be A1

Thanks for participating & looking forward to seeing your great work.
Updates

Hi All. . 

So to reiterate we are looking for one background design to be used for multiple quotes...  The list of quotes are as follows: 

Support and or Sales Office

 

Make your customers feel heard and understood.Make your customers feel respected and liked. Make your customers feelappreciated and helped. Understand that you can do none of these things unlessyou are sincere about them.

Terrence Oakley

 

Nothing liberates our greatness like the desireto help, the desire to serve

Dorothea Quill

 

It’s a very predictable and satisfying phenomenon:whenever we get better, our customers do too.

Cal Pruett

 

Success means we go to sleep at night knowingthat our talents and abilities were used in a way that served others.

Dorothea Quill.

 

The sole purpose of business is to create, serveand satisfy a customer, from beginning to end – and that’s everyone’s job.

Ned Farraday

 

We don’t celebrate closing a sale, we celebrateopening a relationship.

Rosalind Hext

I will never make you a promise – unless I giveyou a plan and procedure to make that promise possible.

Bo Tennant

 

Customers feel we take them for granted; onlyshow interest when we want an order; lavish our time on prospects; communicatemainly by invoice; are fixated on big accounts; drop them like hot potatoesonce we have the order; don’t follow through on promises; and satisfy our ownbureaucracy rather than their needs. We can do better than that, much better.

Alan P Merrow.

 

 

General and public area

 

Catch people in the act of performingextraordinary customer service. Treat them like heroes. Tell their stories, farand wide.

Ned Farraday

 

 

We see our customers as invited guests to aparty, and we are the hosts. It’s our job every day to make every importantaspect of the customer experience a little bit better." Carl Voight - Founder andCEO of Halverin

 

"If you do build a great experience,customers tell each other about that. Word of mouth is verypowerful."  Carl Voight

 

It's not a faithin technology. It's faith in people. Rick Palmer

 

“Being the richest man in the cemetery doesn’tmatter to me … Going to bed at night saying we’ve done something wonderful…that’s what matters to me.” Rick Palmer

 

The customer experience is the next competitivebattleground. Lance Morrow, CIO, Vantor Computers

 

”Do what you do so well that they will want tosee it again and bring their friends.”- Hollis Brandt

In the world of internet customer service, it isimportant to remember your competitor is only a mouse click away. FrankHolden (not sure who he is but like the quote).

The customer is why you go to work. If they goaway, you do, too. Peter Lindqvist (?)

 

MaybeSome for Sales or Build Team:

Quality is remembered long after the price is forgotten. Marzetti Family Slogan

```html
<!DOCTYPE html>
<html lang="en">
<head>
<meta charset="UTF-8">
<title>Nothing Liberates Our Greatness</title>
<link href="https://fonts.googleapis.com/css2?family=Open+Sans:wght@800&family=Poppins:wght@200;600&family=Dancing+Script:wght@700&display=swap" rel="stylesheet">
<style>
  :root {
    --poster-teal: #45e0d2;
    --poster-white: #ffffff;
  }
  html, body {
    margin: 0;
    padding: 0;
    width: 849px;
    height: 1200px;
    overflow: hidden;
    background: var(--poster-teal);
  }
  .poster {
    position: relative;
    width: 849px;
    height: 1200px;
    overflow: hidden;
    background: var(--poster-teal);
    color: var(--poster-white);
  }
  .poster-frame {
    position: absolute;
    left: 20px;
    top: 28px;
    width: 802px;
    height: 1134px;
    border: 1.5px solid var(--poster-white);
    box-sizing: border-box;
  }
  .quote {
    margin: 0;
    padding: 0;
  }
  .quote-line {
    position: absolute;
    left: 0;
    width: 849px;
    margin: 0;
    text-align: center;
    white-space: nowrap;
    line-height: 1;
  }
  .quote-headline {
    top: 230px;
    left: 6px;
    font-family: "Open Sans", sans-serif;
    font-weight: 800;
    font-size: 182px;
    letter-spacing: 0;
    transform: scaleX(0.83);
    transform-origin: center;
  }
  .quote-body {
    font-family: "Poppins", sans-serif;
    font-size: 64px;
    letter-spacing: -1.5px;
  }
  .quote-body .light { font-weight: 200; }
  .quote-body .strong { font-weight: 600; }
  .line-one { top: 443px; left: 5px; }
  .line-two { top: 568px; left: 5px; }
  .line-three { top: 694px; left: 15px; }
  .quote-author {
    position: absolute;
    left: 383px;
    top: 828px;
    margin: 0;
    font-family: "Dancing Script", cursive;
    font-weight: 700;
    font-size: 34px;
    line-height: 1;
    letter-spacing: 1px;
  }
</style>
</head>
<body>
  <main class="poster">
    <div class="poster-frame"></div>
    <blockquote class="quote">
      <p class="quote-line quote-headline">NOTHING</p>
      <p class="quote-line quote-body line-one"><span class="light">Liberates our </span><span class="strong">greatness</span></p>
      <p class="quote-line quote-body line-two"><span class="light">like the </span><span class="strong">desireto help,</span></p>
      <p class="quote-line quote-body line-three"><span class="light">the </span><span class="strong">desire to serve.</span></p>
    </blockquote>
    <p class="quote-author">-Dorothea Quill</p>
  </main>
</body>
</html>
```